Simplified minimalist but bold website

Design a website for a brand 'Brighten Every Day' that shares ideas to make managing home and health easier through email swap series, webinars and eventually courses.

Simple landing page to attract users to sign up for a freebie.

Target Market(s)

women with families & homes to run

Number of Pages Required

1 page

Font styles to use
Sans Serif

Colors
e667a6
b768aa
acd136
ffffff
959595

Requirements
Must have
• Simplified look, line icons, opt-in template, contact us form

```html
<!DOCTYPE html>
<html lang="en">
<head>
<meta charset="utf-8">
<title>Brighten Every Day</title>
<link href="https://fonts.googleapis.com/css2?family=Open+Sans:wght@300;400;600;700;800&family=Poppins:wght@500;600;700&display=swap" rel="stylesheet">
<style>
:root{
  --pink:#e667a6;
  --purple:#b768aa;
  --purple-btn:#a6519a;
  --green:#acd136;
  --blue:#2f96d3;
  --white:#ffffff;
  --grey:#959595;
  --ink:#1e1e1e;
  --text:#3a3a3a;
  --panel-left:#f2f2f2;
  --panel-right:#e5e5e7;
  --footer:#ececec;
  --navy:#1b2a5c;
}
*{box-sizing:border-box;margin:0;padding:0}
html,body{width:1200px;height:2320px;overflow:hidden}
body{position:relative;font-family:"Open Sans",Arial,sans-serif;background:var(--white);color:var(--text)}
.abs{position:absolute}
.center{text-align:center}

/* hero */
.hero{left:0;top:0;width:1200px;height:593px;background:linear-gradient(100deg,#3a3838 0%,#5b5856 35%,#6f6a66 55%,#3f3d3c 100%)}
.hero-shade{left:0;top:0;width:1200px;height:593px;background:rgba(20,20,20,.35)}
.hero-title{left:0;top:78px;width:1200px;font-size:40px;font-weight:700;color:var(--white)}
.hero-rule{left:577px;top:166px;width:46px;height:2px;background:var(--white)}
.hero-sub{left:0;top:220px;width:1200px;font-size:31px;font-weight:300;line-height:41px;color:var(--white)}
.hero-sub strong{font-weight:700}
.scroll-cue{left:575px;top:573px;width:46px;height:46px;border-radius:50%;background:var(--white);box-shadow:0 1px 4px rgba(0,0,0,.25);z-index:2}
.scroll-cue svg{position:absolute;left:14px;top:14px}

/* offer panels */
.panel{top:593px;width:600px;height:718px}
.panel-left{left:0;background:var(--panel-left)}
.panel-right{left:600px;background:var(--panel-right)}
.kicker{width:600px;top:60px;font-size:17px;font-weight:300;letter-spacing:2px;color:#555}
.panel-title{width:600px;top:123px;font-family:"Poppins",Arial,sans-serif;font-size:23px;font-weight:600;color:var(--purple)}
.panel-rule{left:269px;top:173px;width:62px;height:2px;background:var(--pink)}
.lead{width:600px;top:206px;font-size:17px;font-weight:600;color:var(--ink)}
.body-copy{width:600px;top:248px;font-size:15px;line-height:20px;color:#444}
.btn{display:flex;align-items:center;justify-content:center;font-weight:800;color:var(--white);text-transform:uppercase;letter-spacing:.3px}
.btn-sample{left:107px;top:348px;width:174px;height:41px;background:var(--green);font-size:14px}
.btn-learn{left:300px;top:348px;width:173px;height:41px;background:var(--blue);font-size:14px}
.form-label{width:600px;top:437px;font-size:17px;font-weight:600;color:var(--ink)}
.field{width:368px;height:39px;background:var(--white);border:1px solid #cfcfcf;display:flex;align-items:center;padding-left:18px;font-size:13px;color:#444;gap:14px}
.field svg{flex:none}
.btn-submit{width:368px;height:48px;background:var(--purple-btn);font-size:17px}
.notes{left:131px;top:219px;width:347px;height:216px;background:linear-gradient(160deg,#f8f8f8,#dcdcdc);border-radius:4px}

/* series details */
.series-title{left:0;top:1386px;width:1200px;font-size:32px;font-weight:300;color:var(--ink)}
.series-rule{left:568px;top:1455px;width:64px;height:2px;background:var(--pink)}
.series-copy{left:0;width:1200px;font-size:15.5px;line-height:20px;color:#333}
.btn-series{left:444px;top:1790px;width:313px;height:53px;background:var(--purple-btn);font-size:18px}

/* footer */
.footer{left:0;top:1925px;width:1200px;height:395px;background:var(--footer);border-top:3px solid var(--purple)}
.brand{left:142px;top:120px;font-family:"Poppins",Arial,sans-serif;font-size:38px;font-weight:600;color:var(--purple)}
.foot-head{font-size:12px;font-weight:700;color:var(--ink);letter-spacing:.3px}
.foot-item{display:flex;gap:12px;font-size:12px;line-height:17px;color:#222;align-items:flex-start}
.foot-item svg{flex:none;margin-top:2px}
.social{display:flex;align-items:center;gap:12px;font-size:12px;color:#222}
.dot{width:28px;height:28px;border-radius:50%}
.foot-rule{left:142px;top:282px;width:916px;height:1px;background:#cfcfcf}
.copyright{left:0;top:334px;width:1200px;font-size:11.5px;color:#222}
</style>
</head>
<body>

<section class="abs hero" role="img" aria-label="Photo of smiling people shaking hands across a table"></section>
<div class="abs hero-shade"></div>
<h1 class="abs hero-title center">Brighten Every Day.</h1>
<div class="abs hero-rule"></div>
<p class="abs hero-sub center">Chances are life is a little<br>overwhelming. <strong>Let us help</strong></p>
<div class="abs scroll-cue">
  <svg width="18" height="18" viewBox="0 0 18 18" fill="none" stroke="#777" stroke-width="1.6"><path d="M4 4l5 5 5-5M4 9l5 5 5-5"/></svg>
</div>

<section class="abs panel panel-left">
  <p class="abs kicker center">Baby Steps... (try out a few of our tricks)</p>
  <h2 class="abs panel-title center">Swaps Email Series</h2>
  <div class="abs panel-rule"></div>
  <p class="abs lead center">Save TIME, MONEY and SANITY with simple product swaps.</p>
  <p class="abs body-copy center">Reduce the amount of work it takes to run your home.<br>Swap out existing products for more sustainable ones.<br>Each swap saves you work, clutter, time &amp; money.</p>
  <a class="abs btn btn-sample">See Sample Swap</a>
  <a class="abs btn btn-learn">Learn More</a>
  <p class="abs form-label center">Send your ideas my way...</p>
  <div class="abs field" style="left:105px;top:494px">
    <svg width="11" height="12" viewBox="0 0 11 12" fill="#888"><circle cx="5.5" cy="3" r="3"/><path d="M0 12c0-4 2.5-5.5 5.5-5.5S11 8 11 12z"/></svg>NAME</div>
  <div class="abs field" style="left:105px;top:545px">
    <svg width="13" height="10" viewBox="0 0 13 10" fill="#888"><rect width="13" height="10" rx="1"/><path d="M0 1l6.5 5L13 1" stroke="#fff" stroke-width="1.2" fill="none"/></svg>E MAIL</div>
  <a class="abs btn btn-submit" style="left:105px;top:600px">Send Me The Guide!</a>
</section>

<section class="abs panel panel-right">
  <p class="abs kicker center">Big Leap... (I'm ready to roll up my sleeves)</p>
  <h2 class="abs panel-title center">Decluttering Guide</h2>
  <div class="abs panel-rule"></div>
  <div class="abs notes" role="img" aria-label="Illustration of two pinned paper notes about simple steps"></div>
  <div class="abs field" style="left:125px;top:494px">
    <svg width="11" height="12" viewBox="0 0 11 12" fill="#888"><circle cx="5.5" cy="3" r="3"/><path d="M0 12c0-4 2.5-5.5 5.5-5.5S11 8 11 12z"/></svg>NAME</div>
  <div class="abs field" style="left:125px;top:545px">
    <svg width="13" height="10" viewBox="0 0 13 10" fill="#888"><rect width="13" height="10" rx="1"/><path d="M0 1l6.5 5L13 1" stroke="#fff" stroke-width="1.2" fill="none"/></svg>E MAIL</div>
  <a class="abs btn btn-submit" style="left:125px;top:600px">Sign Me Up!</a>
</section>

<h2 class="abs series-title center">Swaps Email Series</h2>
<div class="abs series-rule"></div>
<p class="abs series-copy center" style="top:1507px">Save TIME, MONEY and SANITY with simple product swaps.<br>And reduce the amount of work it takes to run your home.<br>Swap out existing products for more sustainable ones.<br>Each swap save you work, clutter, time &amp; money</p>
<p class="abs series-copy center" style="top:1623px">You get an email 2x weekly for 6-12 weeks only Get<br>even more if you feel they are helpful to you</p>
<p class="abs series-copy center" style="top:1703px">Join our monthly SIMPLE SWAP SHARING web jams with other mums and get even<br>more ideas.Better yet, come with great tips of your own to &nbsp;share.</p>
<a class="abs btn btn-series">Sign Me Up!</a>

<footer class="abs footer">
  <p class="abs brand">Brighten Every Day</p>
  <p class="abs foot-head" style="left:625px;top:75px">CONTACT US</p>
  <div class="abs foot-item" style="left:625px;top:109px">
    <svg width="9" height="12" viewBox="0 0 9 12" fill="#222"><path d="M4.5 0A4.5 4.5 0 0 0 0 4.5C0 8 4.5 12 4.5 12S9 8 9 4.5A4.5 4.5 0 0 0 4.5 0zm0 6.3a1.8 1.8 0 1 1 0-3.6 1.8 1.8 0 0 1 0 3.6z"/></svg>
    <span>58 Maple Row<br>Fairhaven, OH 44210</span></div>
  <div class="abs foot-item" style="left:625px;top:160px">
    <svg width="11" height="11" viewBox="0 0 11 11" fill="#222"><path d="M2.2 0l2 2.5-1.2 1.4a7 7 0 0 0 4.1 4.1L8.5 6.8 11 8.8 9.6 11C4.5 10.6.4 6.5 0 1.4z"/></svg>
    <span>555.208.4412</span></div>
  <div class="abs foot-item" style="left:625px;top:196px">
    <svg width="12" height="9" viewBox="0 0 12 9" fill="#222"><rect width="12" height="9" rx="1"/><path d="M0 1l6 4.5L12 1" stroke="#fff" stroke-width="1.1" fill="none"/></svg>
    <span>hello@brighteneveryday.com</span></div>

  <p class="abs foot-head" style="left:938px;top:75px">CONNECT WITH US</p>
  <div class="abs social" style="left:938px;top:111px"><span class="dot" style="background:#2f4f9a"></span>Homeboard</div>
  <div class="abs social" style="left:938px;top:150px"><span class="dot" style="background:#2aa3e0"></span>Chatline</div>
  <div class="abs social" style="left:938px;top:188px"><span class="dot" style="background:var(--navy)"></span>Worknet</div>

  <div class="abs foot-rule"></div>
  <p class="abs copyright center">Copyrights @ 2018 All Rights Reserved</p>
</footer>

</body>
</html>
```